Need business card with a logo for a hearing aid sales and audiology business. We have two Hearing Instrument Specialists and one Audiologist on staff. Over 25 years in business. Locally owned and operated. Financing available. Most insurances accepted.

Summit Audio Wellness LLC
48730 W Larchmont, Suite 7
Spokane, WA 99281
509-617-2084
www.summitaudiowell.example

Manager
Tobias Kerrell HIS COHC
License #71829046

Target Market(s)

50yr old + people with a hearing loss.

Industry/Entity Type

Business

Contact Information for Business Card

48730 W Larchmont, Suite 7
Spokane, WA 99281
509-617-2084
www.summitaudiowell.example

Manager
Tobias Kerrell HIS COHC
NLVE #71829046

Font styles to use
Serif
Sans Serif

Requirements
Must have
• Business name, Tobias's name and title(s) and contact information, License #, web address

```html
<!DOCTYPE html>
<html lang="en">
<head>
<meta charset="utf-8">
<title>Summit Audio Wellness – Business Card</title>
<link href="https://fonts.googleapis.com/css2?family=Open+Sans:wght@400;600;700&display=swap" rel="stylesheet">
<style>
  :root {
    --backdrop: #e9e7e4;
    --card: #ffffff;
    --navy: #1f3f8c;
    --brand-blue: #0d68b3;
    --ink: #333333;
    --rule: #c9c9c9;
  }
  * { box-sizing: border-box; margin: 0; padding: 0; }
  html, body {
    width: 1200px; height: 1000px; overflow: hidden;
    background: var(--backdrop);
    font-family: "Open Sans", Arial, sans-serif;
  }
  .card {
    position: absolute; left: 100px; top: 201px;
    width: 1000px; height: 598px;
    background: var(--card);
    box-shadow: 0 6px 18px rgba(0,0,0,0.18);
    overflow: hidden;
  }
  .brand {
    position: absolute; right: 47px; top: 100px;
    display: flex; align-items: center; gap: 14px;
    color: var(--brand-blue); font-weight: 600; font-size: 44px; letter-spacing: -0.5px;
  }
  .brand-dot { width: 26px; height: 26px; border-radius: 50%; background: var(--navy); }
  .person { position: absolute; left: 50px; top: 298px; }
  .person-name { color: var(--navy); font-weight: 700; font-size: 31px; letter-spacing: 0.3px; }
  .person-creds { color: var(--brand-blue); font-weight: 400; font-size: 24px; margin-left: 6px; }
  .person-role { color: var(--ink); font-size: 24px; margin-top: -2px; }
  .divider {
    position: absolute; left: 50px; top: 374px; width: 678px; height: 1.5px; background: var(--rule);
  }
  .license { position: absolute; left: 50px; top: 403px; color: var(--ink); font-size: 24px; }
  .contact {
    position: absolute; right: 47px; top: 360px; text-align: right;
    color: var(--ink); font-size: 23px; line-height: 34px;
  }
  .contact-line { display: flex; justify-content: flex-end; align-items: center; gap: 10px; }
  .contact-line svg { width: 22px; height: 22px; }
  .company { font-weight: 700; margin-top: 6px; }
  .address { line-height: 32px; }
  .footer-bands { position: absolute; left: 0; bottom: 0; width: 1000px; height: 44px; }
</style>
</head>
<body>
  <div class="card">
    <div class="brand">
      <span class="brand-dot"></span>
      <span class="brand-name">Summit Audio Wellness</span>
    </div>

    <div class="person">
      <div><span class="person-name">TOBIAS KERRELL</span><span class="person-creds">HIS COHC</span></div>
      <div class="person-role">Manager</div>
    </div>
    <div class="divider"></div>
    <div class="license">License #71829046</div>

    <div class="contact">
      <div class="contact-line">509-617-2084
        <svg viewBox="0 0 24 24" aria-hidden="true"><path fill="#0d68b3" d="M3 9c0-3 4-5 9-5s9 2 9 5v2h-5V9c-1-1-7-1-8 0v2H3zM6 12h12l2 8H4z"/><circle cx="12" cy="16" r="2.2" fill="#fff"/></svg>
      </div>
      <div class="contact-line">www.summitaudiowell.example
        <svg viewBox="0 0 24 24" aria-hidden="true"><circle cx="12" cy="12" r="9" fill="none" stroke="#0d68b3" stroke-width="2.5"/><path d="M3 12h18M12 3c4 4 4 14 0 18M12 3c-4 4-4 14 0 18" fill="none" stroke="#0d68b3" stroke-width="2"/></svg>
      </div>
      <div class="company">Summit Audio Wellness</div>
      <div class="address">48730 W Larchmont, Suite 7</div>
      <div class="address">Spokane, WA 99281</div>
    </div>

    <svg class="footer-bands" viewBox="0 0 1000 44" preserveAspectRatio="none" aria-hidden="true">
      <polygon points="0,16 480,16 458,44 0,44" fill="var(--navy)"/>
      <polygon points="520,0 1000,0 1000,44 476,44" fill="var(--brand-blue)"/>
    </svg>
  </div>
</body>
</html>
```